Quality Monitoring Company Needs a New Site

We are an established company that has a fair number of clients but the site lacks current design standards that we'd like to keep up with. We'd like to mimic the same style of the site on plinkora.com, vetrumo.com, https://brindlecoffer.com/, etc. We'd also like to make sure the designer understands SEO Silos and how it effects the design elements. Attached is the structure that I'd like to follow for the pages. You don't need to design every single sub-page because they'll probably be fairly similar; however, I want to see at least 1 each. Please use the content on our current site for filler areas. Please try to do a good job of understanding what we do so you can use your best judgement on what is needed to be successful. Use our color scheme and the logo should be the side view but I included the AI just in case.
Updates

I am narrowing down on the field of designs that I have received. There are a lot of similarities between the designs I like and don't like. I'd also like to ensure that some of the inner pages get done in the next 5 days so I can see the creativity that is there as well. That is probably what is next -- getting a few inner pages completed so I can see what you can come up with (not based on our current website) because the current "front pages" are all so good and so close.

Industry/Entity Type

Telecommunications

Colors

Designer to choose colors to be used in the design.

Requirements
Must have
• SEO Silo Look and Feel
• Current Colors
Should not have
• No stockphotos whatsoever. NONE.

```html
<!DOCTYPE html>
<html lang="en">
<head>
<meta charset="utf-8">
<title>Sample Scorecards – Veracall</title>
<link href="https://fonts.googleapis.com/css2?family=Montserrat:wght@700&family=Poppins:wght@400;500;600;700&display=swap" rel="stylesheet">
<style>
:root{
  --navy:#0a2d5a;
  --navy-deep:#082b56;
  --cyan:#17a8e3;
  --page:#f5f7fb;
  --ink:#2a2f3a;
  --muted:#5b6170;
  --row-blue:#dbeafb;
  --row-grey:#f3f3f4;
  --rule:#d9dde4;
  --white:#ffffff;
}
*{margin:0;padding:0;box-sizing:border-box}
html,body{width:965px;height:1200px;overflow:hidden}
body{position:relative;background:var(--page);font-family:"Poppins",sans-serif;color:var(--ink)}
.abs{position:absolute}
.rings{position:absolute;left:0;top:0;width:965px;height:440px;pointer-events:none}

.brand{left:112px;top:44px;display:flex;align-items:center;gap:6px}
.brand-dot{width:14px;height:14px;border-radius:50%;background:var(--cyan)}
.brand-name{font-weight:600;font-size:15px;color:var(--navy);letter-spacing:.2px}

.nav{left:325px;top:63px;display:flex;font-size:9.7px;color:var(--ink)}
.nav a{color:inherit;text-decoration:none;position:absolute;white-space:nowrap}

.call{left:727px;top:52px;display:flex;align-items:center;gap:6px}
.call-icon{width:30px;height:30px;border-radius:50%;background:var(--cyan);display:flex;align-items:center;justify-content:center}
.call-num{font-weight:700;font-size:11.4px;color:var(--navy);letter-spacing:.3px}

.hero-title{left:114px;top:180px;font-family:"Montserrat",sans-serif;font-weight:700;font-size:23.5px;color:var(--navy)}
.hero-title span{color:var(--cyan)}
.hero-rule{left:114px;top:219px;width:28px;height:2px;background:var(--cyan)}
.hero-sub{left:116px;top:235px;font-weight:600;font-size:14.8px;color:var(--navy)}
.hero-copy{left:116px;top:262px;width:368px;font-size:9px;line-height:15.4px;letter-spacing:.45px;color:var(--muted)}
.hero-art{left:511px;top:113px;width:326px;height:259px;border-radius:14px;background:linear-gradient(160deg,#bfe4f7 0%,#2cb3e9 55%,#0b3b73 100%);opacity:.9}
.ghost-label{left:465px;top:393px;font-size:10px;color:#ffffff;opacity:.85}

.tabs{left:0;top:471px;width:965px;height:34px}
.tab{position:absolute;top:0;height:34px;transform:translateX(-50%);text-align:center;font-size:9.1px;line-height:10.6px;color:var(--muted);display:flex;align-items:center;justify-content:center;white-space:nowrap}
.tab.active{background:var(--navy);color:var(--white);border-radius:17px;width:96px;box-shadow:0 5px 10px rgba(10,45,90,.25)}

.card{left:142px;top:528px;width:681px;height:346px;background:var(--white);box-shadow:0 6px 30px rgba(20,40,80,.05)}
.score{position:absolute;left:11px;top:12px;width:659px;border-collapse:collapse;table-layout:fixed}
.score th{background:var(--navy);color:var(--white);font-weight:600;font-size:11.4px;height:34px;text-align:left;padding-left:17px;border-right:1px solid #3a5a84}
.score th.c{text-align:center;padding-left:0}
.score th:last-child{border-right:none}
.score td{height:31.2px;font-size:9.1px;font-weight:500;letter-spacing:.3px;padding-left:17px;border-right:1px solid var(--rule);color:var(--ink)}
.score td:last-child{border-right:none}
.score tr:nth-child(odd) td{background:var(--row-grey)}
.score tr:nth-child(even) td{background:var(--white)}
.score tr.hl td{background:var(--row-blue)}

.footer{left:0;top:984px;width:965px;height:216px;background:var(--navy-deep);color:var(--white)}
.f-head{position:absolute;top:45px;font-weight:700;font-size:13.6px;color:var(--cyan);font-family:"Montserrat",sans-serif}
.f-links{position:absolute;top:74px;font-size:9.1px;line-height:16.3px}
.f-item{position:absolute;display:flex;align-items:flex-start;gap:6px;font-size:10.2px;line-height:19px}
.f-brand{position:absolute;left:752px;top:50px;display:flex;align-items:center;gap:8px}
.f-brand-dot{width:22px;height:22px;border-radius:50%;background:var(--cyan)}
.f-brand-name{font-weight:600;font-size:20px;color:var(--white)}
.f-rule{position:absolute;left:112px;top:178px;width:738px;height:1px;background:#2a4d7a}
.f-copy{position:absolute;left:0;top:189px;width:965px;text-align:center;font-size:9.6px}
</style>
</head>
<body>

<svg class="rings" viewBox="0 0 965 440" aria-hidden="true">
  <circle cx="830" cy="120" r="320" fill="none" stroke="#e6f2fc" stroke-width="40" opacity=".7"/>
  <circle cx="830" cy="120" r="240" fill="none" stroke="#dcebfa" stroke-width="50" opacity=".8"/>
  <circle cx="830" cy="120" r="175" fill="#f3f8fd"/>
</svg>

<div class="abs brand"><span class="brand-dot"></span><span class="brand-name">Veracall</span></div>

<nav class="abs nav">
  <a style="left:0">Home</a>
  <a style="left:47px">Services</a>
  <a style="left:107px">Industries</a>
  <a style="left:173px">Pricing</a>
  <a style="left:224px">Team</a>
  <a style="left:272px">Blog</a>
  <a style="left:312px">Contact Us</a>
</nav>

<div class="abs call">
  <span class="call-icon">
    <svg width="13" height="13" viewBox="0 0 24 24"><path fill="#fff" d="M6.6 10.8a15.1 15.1 0 0 0 6.6 6.6l2.2-2.2a1 1 0 0 1 1-.25 11.4 11.4 0 0 0 3.6.57 1 1 0 0 1 1 1V20a1 1 0 0 1-1 1A17 17 0 0 1 3 4a1 1 0 0 1 1-1h3.5a1 1 0 0 1 1 1c0 1.25.2 2.45.57 3.57a1 1 0 0 1-.25 1z"/></svg>
  </span>
  <span class="call-num">555-014-2277</span>
</div>

<h1 class="abs hero-title">Sample <span>Scorecards</span></h1>
<div class="abs hero-rule"></div>
<h2 class="abs hero-sub">Can Voice Analytics Do This?</h2>
<p class="abs hero-copy">Veracall’s quality assurance services cut across key industry verticals. We have the capability to customize scorecards to suit your specific industry and provide an integrated solution for diverse and geographically split processes.</p>
<div class="abs hero-art" role="img" aria-label="Illustration of a rocket launching from a laptop screen, surrounded by leaves, a gear, a document badge and a paper plane"></div>
<div class="abs ghost-label">Mortgage</div>

<div class="abs tabs">
  <div class="tab active" style="left:148px">Call Tracking<br>Automotive</div>
  <div class="tab" style="left:240px">Call Tracking<br>General</div>
  <div class="tab" style="left:318px">Not<br>interested</div>
  <div class="tab" style="left:389px">Mortgage<br>Sector</div>
  <div class="tab" style="left:458px">Insurance<br>Sector</div>
  <div class="tab" style="left:524px">Home<br>Services</div>
  <div class="tab" style="left:589px">Home<br>Warranty</div>
  <div class="tab" style="left:660px">Healthcare<br>Sector</div>
  <div class="tab" style="left:732px">Customer<br>Service</div>
  <div class="tab" style="left:813px">Debt<br>Consolidation</div>
</div>

<div class="abs card">
  <table class="score">
    <colgroup><col style="width:117px"><col style="width:153px"><col style="width:254px"><col style="width:48px"><col style="width:44px"><col style="width:43px"></colgroup>
    <thead><tr><th>Section</th><th>Short Name</th><th>Long Question</th><th class="c">YES</th><th class="c">NO</th><th class="c">NA</th></tr></thead>
    <tbody>
      <tr class="hl"><td>Questionnaire</td><td>Define the caller</td><td>Was the caller a customer or client?</td><td></td><td></td><td></td></tr>
      <tr><td>Questionnaire</td><td>New Product Inquiry</td><td>Did the caller inquire about a new product?</td><td></td><td></td><td></td></tr>
      <tr><td>Questionnaire</td><td>Lease Product Inquiry</td><td>Did the caller inquire about leasing?</td><td></td><td></td><td></td></tr>
      <tr><td>Questionnaire</td><td>Parts and Service</td><td>Did the caller asked for parts and service?</td><td></td><td></td><td></td></tr>
      <tr><td>Questionnaire</td><td>Appointment Scheduled</td><td>Was an appointment scheduled?</td><td></td><td></td><td></td></tr>
      <tr class="hl"><td>Questionnaire</td><td>Price Inquiry</td><td>Was there a price inquiry?</td><td></td><td></td><td></td></tr>
      <tr><td>Questionnaire</td><td>Testing Scheduled</td><td>Was testing scheduled?</td><td></td><td></td><td></td></tr>
      <tr><td>Questionnaire</td><td>Luxury package selected</td><td>Was the luxury package scheduled?</td><td></td><td></td><td></td></tr>
      <tr><td>Questionnaire</td><td>Information provided</td><td>Was caller information provided?</td><td></td><td></td><td></td></tr>
    </tbody>
  </table>
</div>

<footer class="abs footer">
  <div class="f-head" style="left:112px">Quick Links</div>
  <div class="f-links" style="left:112px">Home<br>Services<br>System Details<br>Pricing</div>
  <div class="f-links" style="left:236px">Team<br>Blog<br>Contact Us<br>Login</div>

  <div class="f-head" style="left:370px">Contact Us</div>
  <div class="f-item" style="left:372px;top:72px">
    <svg width="9" height="13" viewBox="0 0 24 32" style="margin-top:4px"><path fill="#fff" d="M12 0A11 11 0 0 0 1 11c0 8 11 21 11 21s11-13 11-21A11 11 0 0 0 12 0zm0 15a4 4 0 1 1 0-8 4 4 0 0 1 0 8z"/></svg>
    <span>2870 Marlowe Blvd.<br>Riverton, CA 90412</span>
  </div>
  <div class="f-item" style="left:531px;top:72px">
    <svg width="11" height="11" viewBox="0 0 24 24" style="margin-top:5px"><path fill="#fff" d="M6.6 10.8a15.1 15.1 0 0 0 6.6 6.6l2.2-2.2a1 1 0 0 1 1-.25 11.4 11.4 0 0 0 3.6.57 1 1 0 0 1 1 1V20a1 1 0 0 1-1 1A17 17 0 0 1 3 4a1 1 0 0 1 1-1h3.5a1 1 0 0 1 1 1c0 1.25.2 2.45.57 3.57a1 1 0 0 1-.25 1z"/></svg>
    <span>555-014-2277</span>
  </div>
  <div class="f-item" style="left:531px;top:100px">
    <svg width="12" height="9" viewBox="0 0 24 18" style="margin-top:6px"><path fill="#fff" d="M0 0h24v2L12 10 0 2zM0 4.5l12 8 12-8V18H0z"/></svg>
    <span>hello@veracall.com</span>
  </div>

  <div class="f-brand"><span class="f-brand-dot"></span><span class="f-brand-name">Veracall</span></div>

  <div class="f-rule"></div>
  <div class="f-copy">Copyright © 2019 VERACALL. All Rights Reserved.</div>
</footer>

</body>
</html>
```